KR Appraisals website redesign

I would like to refresh my existing website of www.krappraisals-example.com with new graphics, look and feel, as well as updated structure and wording. Content and layout changes have been uploaded to this project Brief.

My existing website has a dark feel. I am now looking for a light and energetic feel. Financial Services is my industry, so the website should be reflect that. I would also like to reflect the concepts of Trust, Service and Expertise.

The website must be serious and upmarket.

Target Market(s)

Corporate board members, CFO's, treasurers and controllers
Auditors, tax advisors, private equity and venture capital asset managers, investors, tax authorities

Industry/Entity Type

Financial Service

Coding

Coded - Design and coding required

Number of Pages Required

5+ page

Font styles to use
Sans Serif
Other font styles liked:
• Designer can choose another modern font

Colors
0355a3
3277b5
85acd3
eaf1f7
f37122
f68d4d
9bcb3c
acd037
cadf82

Requirements
Must have
• Good hi resolution pictures that convey "Finance", "Trust", "Service" or "Expertise".
• An anti-bot (such as Captcha) mechanism in the contact form.
Should not have
• Must not have all content on one rolling screen.

```html
<!DOCTYPE html>
<html lang="en">
<head>
<meta charset="utf-8">
<title>KR Appraisals – Business &amp; Intellectual Property Appraisals</title>
<link rel="stylesheet" href="https://fonts.googleapis.com/css2?family=Cinzel:wght@700;900&family=Roboto:wght@300;400;500&display=swap">
<style>
:root{
  --ink:#1c1c1c;
  --text:#5a5a5a;
  --heading:#1a1a1a;
  --grey-mark:#6b6b6b;
  --blue-deep:#0355a3;
  --blue:#3277b5;
  --blue-soft:#85acd3;
  --blue-pale:#eaf1f7;
  --slate:#33495c;
  --news-bg:#f1f1f1;
  --footer:#000;
  --white:#fff;
}
*{box-sizing:border-box;margin:0;padding:0}
html,body{width:1200px;height:4204px;overflow:hidden;background:var(--white)}
body{font-family:"Roboto",Arial,sans-serif;color:var(--text)}
.page{position:relative;width:1200px;height:4204px;overflow:hidden}
.abs{position:absolute}
.display{font-family:"Cinzel",Georgia,serif;font-weight:700;color:var(--heading);letter-spacing:1px}

/* header */
.site-header{position:absolute;top:0;left:0;width:1200px;height:100px;background:var(--white);z-index:3}
.brand{position:absolute;left:90px;top:52px;height:34px;padding:0 8px;border:2px solid #555;display:flex;align-items:center;font-size:22px;font-weight:400;color:#555}
.nav{position:absolute;top:38px;left:526px;display:flex;gap:0}
.nav a{font-size:17px;font-weight:500;color:#333;text-decoration:none;margin-right:35px}

/* hero */
.hero{position:absolute;top:100px;left:0;width:1200px;height:620px;overflow:hidden}
.hero-photo{position:absolute;inset:0;background:linear-gradient(160deg,#eef3f8 0%,#cfdeee 35%,#9fc0e2 60%,#d9e5f1 100%)}
.hero-title{position:absolute;top:168px;left:0;width:1200px;text-align:center;font-size:60px;line-height:66px;font-weight:900;color:#151515}
.hero-dots{position:absolute;top:388px;left:557px;display:flex;gap:12px}
.hero-dots span{width:12px;height:12px;border-radius:50%;background:#777}
.hero-dots span:first-child{background:#111}
.hero-wave{position:absolute;left:0;top:0}

/* services */
.section-title{position:absolute;left:0;width:1200px;text-align:center;font-size:44px}
.swoosh{position:absolute}
.service{position:absolute;width:300px}
.service h3{font-size:21px;font-weight:400;color:#333;margin-bottom:8px}
.service p{font-size:15.5px;line-height:28.5px;font-weight:300;color:#555}
.service.left{text-align:right}
.service.left h3{padding-right:18px;border-right:2px solid #666;display:inline-block;line-height:24px}
.service.right h3{padding-left:18px;border-left:2px solid #666;display:inline-block;line-height:24px}
.service.right p{padding-left:20px}
.service.left p{padding-right:22px}
.service-icon{position:absolute;width:40px;height:40px;border:2px solid #555;border-radius:6px;background:#f6f6f6}
.center-name{position:absolute;left:440px;top:1100px;width:320px;text-align:center;font-size:52px;font-weight:500;color:var(--grey-mark)}

/* trust */
.trust{position:absolute;left:0;top:1525px}
.trust-copy{position:absolute;left:88px;top:1718px;width:630px;color:#eaeef2}
.trust-copy h2{font-size:42px;line-height:56px;color:var(--white)}
.trust-copy p{font-size:14.5px;line-height:28px;font-weight:300;margin-bottom:30px}
.trust-copy a{font-size:12.5px;color:#eaeef2;font-style:italic;text-decoration:underline;letter-spacing:.2px}

/* about */
.about-name{position:absolute;left:160px;top:2490px;width:370px;text-align:center;font-size:54px;font-weight:500;color:var(--blue-deep)}
.about-copy{position:absolute;left:622px;top:2345px;width:490px}
.about-copy h2{font-size:44px;margin-bottom:26px}
.about-copy p{font-size:14.5px;line-height:33px;font-weight:300;color:#555;text-align:justify}
.btn{display:inline-block;margin-top:18px;width:155px;height:50px;line-height:50px;border-radius:25px;background:#111;color:var(--white);text-align:center;font-size:14px;font-weight:500;letter-spacing:.3px}

/* news */
.news{position:absolute;left:0;top:2832px;width:1200px;height:900px;background:var(--news-bg)}
.card{position:absolute;top:3030px;width:304px;height:467px;background:var(--white);border-radius:44px 44px 0 0;box-shadow:0 4px 14px rgba(0,0,0,.12);overflow:hidden}
.card-media{position:absolute;left:10px;top:10px;width:284px;height:232px;border-radius:38px 38px 0 0}
.card-date{position:absolute;left:28px;top:270px;font-size:12.5px;color:#777;display:flex;align-items:center;gap:8px}
.card-date i{width:12px;height:12px;border:1.5px solid #999;border-radius:2px;display:inline-block}
.card h3{position:absolute;left:28px;top:305px;width:255px;font-size:17px;line-height:31px;font-weight:500;color:#222}
.card-arrow{position:absolute;right:34px;bottom:26px}

/* footer */
.footer-wave{position:absolute;left:0;top:3580px}
.footer{position:absolute;left:0;top:3790px;width:1200px;height:414px;background:var(--footer);color:var(--white)}
.rule{position:absolute;left:215px;width:770px;height:1px;background:#333}
.office{position:absolute;top:110px;width:260px;text-align:center;font-size:14.5px;line-height:28px}
.office h4{font-size:15px;font-weight:500;margin-bottom:22px}
.vline{position:absolute;top:110px;width:1px;height:130px;background:#444}
.badge{position:absolute;background:#d9d9d9}
.social{position:absolute;top:326px;left:518px;display:flex;gap:8px}
.social span{width:34px;height:34px;border:1.5px solid #fff;border-radius:50%}
.copyright{position:absolute;top:373px;left:0;width:1200px;text-align:center;font-size:12px;color:#ddd}
</style>
</head>
<body>
<div class="page">

  <header class="site-header">
    <div class="brand">KR Appraisals</div>
    <nav class="nav">
      <a href="#">Home</a><a href="#">Services</a><a href="#">News &amp; Views</a><a href="#">About</a><a href="#">Careers</a><a href="#">Contact</a>
    </nav>
  </header>

  <section class="hero">
    <div class="hero-photo" role="img" aria-label="Desk covered with blue financial charts and reports, with a pen"></div>
    <h1 class="hero-title display">Business &amp; Intellectual<br>Property Valuations</h1>
    <div class="hero-dots"><span></span><span></span><span></span><span></span></div>
    <svg class="hero-wave" width="1200" height="620" viewBox="0 0 1200 620" aria-hidden="true">
      <path d="M0 520 C150 590 300 600 480 560 C700 500 900 440 1200 450 L1200 620 L0 620 Z" fill="#2b2b2b"/>
      <path d="M0 532 C160 604 320 612 500 574 C720 524 920 476 1200 520 L1200 620 L0 620 Z" fill="#ffffff"/>
    </svg>
  </section>

  <h2 class="section-title display" style="top:800px">Our Services</h2>
  <svg class="swoosh" style="left:565px;top:866px" width="70" height="10" viewBox="0 0 70 10" aria-hidden="true"><path d="M0 7 C20 1 50 1 70 4 C50 4 25 5 0 7Z" fill="#444"/></svg>

  <div class="service left" style="left:98px;top:930px"><h3>Transaction Support</h3><p>Acquisition, divestment and investment valuations to help you maximize your investment returns.</p></div>
  <div class="service-icon" role="img" aria-label="Transaction icon" style="left:437px;top:925px"></div>

  <div class="service-icon" role="img" aria-label="Training icon" style="left:722px;top:925px"></div>
  <div class="service right" style="left:785px;top:930px"><h3>Finance Training</h3><p>Open-enrollment training to the professional finance and banking markets</p></div>

  <div class="service left" style="left:36px;top:1091px"><h3>Fiscal Valuations</h3><p>Business valuations to support Dutch participation exemption, capital gains and significant impairment tests</p></div>
  <div class="service-icon" role="img" aria-label="Fiscal icon" style="left:376px;top:1086px"></div>

  <div class="center-name">KR Appraisals</div>

  <div class="service-icon" role="img" aria-label="Advisory icon" style="left:785px;top:1086px"></div>
  <div class="service right" style="left:848px;top:1091px"><h3>Capital Advisory</h3><p>Analysis and assessment of strategic options from a valuation and financial perspective</p></div>

  <div class="service left" style="left:70px;top:1270px"><h3>Financial Reporting</h3><p>Purchase price allocations (PPA), goodwill analyses, impairment testing, intangible asset valuations and share plan valuations for IFRS, Dutch GAAP and US GAAP accounting purposes</p></div>
  <div class="service-icon" role="img" aria-label="Reporting icon" style="left:413px;top:1265px"></div>

  <div class="service-icon" role="img" aria-label="Legal icon" style="left:760px;top:1265px"></div>
  <div class="service right" style="left:815px;top:1270px"><h3>Legal Support</h3><p>Business valuations relating to contribution in kind statements “inbrengverklaring” when a company is initially funded with equity</p></div>

  <svg class="trust" width="1200" height="720" viewBox="0 0 1200 720" role="img" aria-label="Businessman using a tablet in front of glowing financial bar charts">
    <defs>
      <linearGradient id="trustFill" x1="0" y1="0" x2="1" y2="0">
        <stop offset="0" stop-color="#3a4c5c"/>
        <stop offset=".5" stop-color="#2f4558"/>
        <stop offset=".75" stop-color="#2a5f86"/>
        <stop offset="1" stop-color="#13243a"/>
      </linearGradient>
    </defs>
    <path d="M0 110 C200 150 380 120 560 70 C760 15 980 -20 1200 30 L1200 590 C1000 560 850 600 700 650 C500 715 250 720 0 670 Z" fill="url(#trustFill)"/>
  </svg>
  <div class="trust-copy">
    <h2 class="display">Trust, Service &amp;<br>Expertise</h2>
    <svg width="70" height="12" viewBox="0 0 70 12" style="margin:6px 0 18px" aria-hidden="true"><path d="M0 9 C20 1 50 1 70 5 C50 5 25 6 0 9Z" fill="#fff"/></svg>
    <p>Trust is paramount. Clients rely on KR Appraisal Services for confidentiality, transparency and independence.</p>
    <p>Service is front and center in KR Appraisal Services’ product offerings. KR Appraisal Services considers the needs of all stakeholders and the personal needs of the client team involved.</p>
    <p>KR Appraisal Services offers more than a decade of valuation experience and maintains its commitment to continual professional development.</p>
    <a href="#">CLICK HERE TO DOWNLOAD OUR BROCHURE</a>
  </div>

  <div class="about-name">KR Appraisals</div>
  <div class="about-copy">
    <h2 class="display">About Us</h2>
    <svg width="70" height="12" viewBox="0 0 70 12" style="position:absolute;left:0;top:62px" aria-hidden="true"><path d="M0 9 C20 1 50 1 70 5 C50 5 25 6 0 9Z" fill="#444"/></svg>
    <p>KR Appraisals, founded in 2012, is a boutique valuation advisory practice servicing companies throughout Europe and North America. We have offices in Leiden and Amsterdam. Through our affiliate partners, we also have offices in New York and London offering transfer pricing, derivatives modelling, and machinery &amp; equipment valuation. Our clients come from a broad range of industries with valuations ranging between micro-cap and large-cap.</p>
    <span class="btn">READ MORE</span>
  </div>

  <section class="news"></section>
  <h2 class="section-title display" style="top:2925px">News &amp;Views</h2>
  <svg class="swoosh" style="left:565px;top:2990px" width="70" height="10" viewBox="0 0 70 10" aria-hidden="true"><path d="M0 7 C20 1 50 1 70 4 C50 4 25 5 0 7Z" fill="#444"/></svg>

  <article class="card" style="left:93px">
    <div class="card-media" role="img" aria-label="Hands signing a document over a chart" style="background:linear-gradient(135deg,#c9c4b6,#e8e9ec 55%,#a9b8c8)"></div>
    <div class="card-date"><i></i>March 9, 2016</div>
    <h3>Dutch GAAP Update – Goodwill and Definitions of Value</h3>
    <svg class="card-arrow" width="38" height="16" viewBox="0 0 38 16" aria-hidden="true"><path d="M0 8H36M29 1l7 7-7 7" fill="none" stroke="#444" stroke-width="1.6"/></svg>
  </article>
  <article class="card" style="left:450px">
    <div class="card-media" role="img" aria-label="Hand using a smartphone at a desk" style="background:linear-gradient(135deg,#6d5a43,#c9b27a 50%,#ece6d8)"></div>
    <div class="card-date"><i></i>February 4, 2016</div>
    <h3>Daniel Hart to Speak at Route2West on Feb 18 in Oosterhout, the Netherlands</h3>
    <svg class="card-arrow" width="38" height="16" viewBox="0 0 38 16" aria-hidden="true"><path d="M0 8H36M29 1l7 7-7 7" fill="none" stroke="#444" stroke-width="1.6"/></svg>
  </article>
  <article class="card" style="left:807px">
    <div class="card-media" role="img" aria-label="City skyline seen through office windows" style="background:linear-gradient(180deg,#7fa3c1,#e8c48e 55%,#3c6470)"></div>
    <div class="card-date"><i></i>February 4, 2016</div>
    <h3>KR Appraisals presenteert bij Route2West op 18 februari in Oosterhout</h3>
    <svg class="card-arrow" width="38" height="16" viewBox="0 0 38 16" aria-hidden="true"><path d="M0 8H36M29 1l7 7-7 7" fill="none" stroke="#444" stroke-width="1.6"/></svg>
  </article>

  <svg class="footer-wave" width="1200" height="220" viewBox="0 0 1200 220" aria-hidden="true">
    <rect x="0" y="0" width="1200" height="220" fill="#fff"/>
    <path d="M0 130 C150 190 330 190 520 130 C760 55 980 40 1200 100 L1200 220 L0 220 Z" fill="#9a9a9a"/>
    <path d="M0 140 C160 200 340 200 530 145 C770 75 990 75 1200 120 L1200 220 L0 220 Z" fill="#000"/>
  </svg>

  <footer class="footer">
    <div class="rule" style="top:112px"></div>
    <div class="rule" style="top:242px"></div>
    <div class="office" style="left:222px;top:110px;padding-top:14px"><h4>Leiden</h4>Veldstraat 14<br>2311 Kx Leiden<br>Tel: 070 555 0142</div>
    <div class="vline" style="left:485px"></div>
    <div class="badge" role="img" aria-label="Professional membership badge" style="left:525px;top:138px;width:150px;height:26px;border-radius:4px"></div>
    <div class="badge" role="img" aria-label="Professional membership badge" style="left:525px;top:180px;width:150px;height:46px;border-radius:4px"></div>
    <div class="vline" style="left:715px"></div>
    <div class="office" style="left:718px;top:110px;padding-top:14px"><h4>Amsterdam</h4>Keizerskade 38<br>1016 Bt Amsterdam<br>Tel: 020 555 0187</div>
    <div class="social"><span></span><span></span><span></span><span></span></div>
    <div class="copyright">©2019 KR Appraisals Logo by Mara Lindqvist Website by Pixelvane</div>
  </footer>

</div>
</body>
</html>
```